Youth deer hunt give away flyer.

We need a flyer designed for a youth deer hunt giveaway that we are doing. We are an Illinois whitetail deer hunting outfitter. We house and feed our clients as well as providing them with a guided deer hunt. It needs to include images as well as details about the giveaway. Im looking for a proffesional, looking flyer
Updates

Target Market(s)

rednecks, hunters

Industry/Entity Type

Hunting

Font styles to use
Serif
Sans Serif

Colors
000000
dbdbdb
ffffff
474747

Requirements
Must have
• not sure
Nice to have
• not sure
Should not have
• not sure

```html
<!DOCTYPE html>
<html lang="en">
<head>
<meta charset="utf-8">
<title>2018 Youth Firearm Hunt – Harlan Farms Outfitting</title>
<link href="https://fonts.googleapis.com/css2?family=Cinzel:wght@400;600&family=Lato:wght@400;700&display=swap" rel="stylesheet">
<style>
  :root {
    --black: #000000;
    --ink: #1d1d1d;
    --charcoal: #2b2b2b;
    --slate: #474747;
    --mist: #dbdbdb;
    --white: #ffffff;
    --stage: #ebe9e6;
    --forest-dark: #3a2412;
    --forest-mid: #7a4a1e;
    --forest-light: #a8702e;
    --field-green: #5d7a3a;
  }
  * { box-sizing: border-box; margin: 0; padding: 0; }
  html, body {
    width: 1200px; height: 1200px; overflow: hidden;
    background: var(--stage);
  }
  .flyer {
    position: absolute; left: 215px; top: 30px;
    width: 770px; height: 1140px; overflow: hidden;
    background: linear-gradient(180deg, #f4f4f4 0%, #ffffff 45%, #eeeeee 80%, var(--mist) 100%);
    box-shadow: 0 4px 18px rgba(0,0,0,.18);
    font-family: "Lato", sans-serif;
    color: var(--ink);
  }
  .flyer__art { position: absolute; inset: 0; width: 770px; height: 1140px; }

  .brand-badge {
    position: absolute; left: 504px; top: 173px; width: 214px; height: 214px;
    border-radius: 50%; background: var(--charcoal);
    border: 5px solid var(--white);
    display: flex; align-items: center; justify-content: center; text-align: center;
  }
  .brand-badge__name {
    font-family: "Cinzel", serif; font-weight: 400; font-size: 19px;
    line-height: 1.25; color: var(--white); letter-spacing: .5px;
  }

  .event-title { position: absolute; left: 55px; top: 400px; font-family: "Cinzel", serif; font-weight: 400; }
  .event-title__year { display: block; font-size: 50px; color: var(--ink); line-height: 1.05; }
  .event-title__name { display: block; font-size: 62px; color: var(--slate); line-height: 1.1; margin-left: 4px; }

  .hunt-details { position: absolute; left: 68px; top: 537px; width: 300px; list-style: none; }
  .hunt-details li {
    position: relative; padding-left: 20px; font-size: 15px; line-height: 1.3;
    color: var(--ink); margin-bottom: 14px;
  }
  .hunt-details li::before {
    content: ""; position: absolute; left: 2px; top: 7px;
    width: 6px; height: 6px; border-radius: 50%; background: var(--ink);
  }
  .hunt-details .hunt-details__date { font-weight: 700; font-size: 17px; margin-bottom: 12px; }

  .about { position: absolute; left: 440px; top: 600px; width: 280px; color: var(--white); }
  .about__heading { font-family: "Cinzel", serif; font-size: 16px; letter-spacing: .5px; margin-bottom: 9px; }
  .about__body { font-size: 10.6px; line-height: 1.33; text-align: justify; }

  .contact { position: absolute; left: 297px; top: 1000px; color: var(--white); }
  .contact__name { font-family: "Cinzel", serif; font-size: 16px; letter-spacing: .5px; margin-bottom: 7px; }
  .contact__list { list-style: none; font-size: 12px; line-height: 1.3; }
  .contact__list li { display: flex; align-items: flex-start; gap: 9px; margin-bottom: 4px; }
  .contact__list svg { width: 10px; height: 10px; margin-top: 3px; flex: none; fill: var(--white); }

  .social { position: absolute; left: 486px; top: 1088px; display: flex; align-items: center; gap: 10px; }
  .social__rule { width: 56px; height: 1px; background: #888; }
  .social__dot { width: 20px; height: 20px; border-radius: 50%; background: var(--white); }
</style>
</head>
<body>
<main class="flyer">
  <svg class="flyer__art" viewBox="0 0 770 1140" xmlns="http://www.w3.org/2000/svg">
    <defs>
      <linearGradient id="forestTone" x1="0" y1="0" x2="1" y2="1">
        <stop offset="0" stop-color="var(--forest-dark)"/>
        <stop offset=".45" stop-color="var(--forest-mid)"/>
        <stop offset=".75" stop-color="var(--forest-light)"/>
        <stop offset="1" stop-color="var(--forest-dark)"/>
      </linearGradient>
      <linearGradient id="swoosh" x1="0" y1="0" x2="1" y2="0">
        <stop offset="0" stop-color="#bdbdbd"/>
        <stop offset=".5" stop-color="var(--black)"/>
        <stop offset="1" stop-color="#9a9a9a"/>
      </linearGradient>
      <linearGradient id="fieldTone" x1="0" y1="0" x2="0" y2="1">
        <stop offset="0" stop-color="#b8b0a6"/>
        <stop offset=".55" stop-color="#8a6a46"/>
        <stop offset="1" stop-color="#5b4a36"/>
      </linearGradient>
      <linearGradient id="cabinTone" x1="0" y1="0" x2="0" y2="1">
        <stop offset="0" stop-color="#e4e8ea"/>
        <stop offset=".55" stop-color="#c08a3e"/>
        <stop offset="1" stop-color="var(--field-green)"/>
      </linearGradient>
    </defs>

    <!-- header swoosh under the photo band -->
    <path d="M30 120 Q390 640 700 150 Q390 590 30 120 Z" fill="url(#swoosh)"/>
    <path d="M40 110 Q390 660 720 140 L730 150 Q390 700 30 120 Z" fill="url(#swoosh)" opacity=".85"/>

    <!-- header photo band -->
    <path d="M0 0 H770 V90 Q390 560 0 90 Z" fill="url(#forestTone)" role="img"
          aria-label="Photo: a hunter kneeling in autumn woods holding the antlers of a large whitetail buck"/>

    <!-- footer dark panel -->
    <path d="M190 1140 V955 Q420 890 570 990 Q690 1070 770 1098 V1140 Z" fill="var(--charcoal)"/>
    <path d="M230 940 Q430 880 580 975 Q700 1055 770 1085 V1093 Q690 1065 570 985 Q430 895 230 945 Z" fill="var(--white)"/>

    <!-- about us brush panel -->
    <path d="M417 575 L470 569 L520 576 L590 567 L660 574 L725 566 L735 590 L728 640 L737 700 L729 760 L736 815 L722 840 L660 836 L600 845 L540 834 L470 846 L423 838 L430 800 L421 740 L428 680 L419 620 Z" fill="var(--ink)"/>

    <!-- footer photo: hunter with buck -->
    <path d="M15 1140 V800 Q160 760 320 800 V1140 Z" fill="url(#fieldTone)" role="img"
          aria-label="Photo: a young hunter in an orange cap posing beside a harvested whitetail buck"/>

    <!-- circle photos -->
    <circle cx="544" cy="942" r="80" fill="var(--charcoal)"/>
    <circle cx="544" cy="942" r="74" fill="url(#cabinTone)" role="img" aria-label="Photo: the private log cabin guests stay in"/>
    <circle cx="643" cy="1019" r="60" fill="var(--charcoal)"/>
    <circle cx="643" cy="1019" r="54" fill="url(#forestTone)" role="img" aria-label="Photo: a hunter sitting with a buck in the woods"/>
  </svg>

  <div class="brand-badge">
    <span class="brand-badge__name">Harlan Farms<br>Outfitting</span>
  </div>

  <h1 class="event-title">
    <span class="event-title__year">2018 Youth</span>
    <span class="event-title__name">Firearm Hunt</span>
  </h1>

  <ul class="hunt-details">
    <li class="hunt-details__date">October 6-8, 2018</li>
    <li>4 night stay in our private cabin that include meals for 2 parents and the child.</li>
    <li>Guided shotgun hunt on strictly managed properties.</li>
    <li>Ground blinds in place</li>
    <li>Permit and license fees are the hunters responsibility.</li>
  </ul>

  <section class="about">
    <h2 class="about__heading">About us</h2>
    <p class="about__body">Harlan Farms Outfitting is a family owned and operated deer hunting outfitter located in Morgan and Scott Counties in west central Illinois. We provide low pressure, trophy whitetail hunts on privately owned farms across the region. The Harlans are lifelong residents and hunters of Morgan County, with the family farm being established well over 150 years ago.<br>To go along with guiding deer and turkey hunters, we also offer a wide variety of professional hunting services that include whitetail land consulting, scouting services, CRP and food plot plantings and more.</p>
  </section>

  <address class="contact" style="font-style:normal">
    <p class="contact__name">Wade Harlan</p>
    <ul class="contact__list">
      <li><svg viewBox="0 0 10 10"><path d="M2 0.5 L3.6 2.6 L2.7 3.6 Q3.6 5.8 6.4 7.3 L7.4 6.4 L9.5 8 L8.3 9.5 Q3 9 0.5 1.7 Z"/></svg>(555) 014-2290</li>
      <li><svg viewBox="0 0 10 10"><path d="M1 5 L9 1 L6 9 L5 6 Z"/></svg>www.harlanfarmsoutfitting.example</li>
      <li><svg viewBox="0 0 10 10"><path d="M0.5 2 H9.5 V8 H0.5 Z M0.5 2 L5 5.5 L9.5 2" stroke="var(--charcoal)" stroke-width=".8"/></svg>hello@harlanfarms.example</li>
      <li><svg viewBox="0 0 10 10"><path d="M5 0.5 A3.2 3.2 0 0 1 8.2 3.7 Q8.2 6 5 9.5 Q1.8 6 1.8 3.7 A3.2 3.2 0 0 1 5 0.5 Z"/></svg>840 Cedar Lane<br>Millbrook, Illinois 62000</li>
    </ul>
  </address>

  <div class="social" aria-label="Social media">
    <span class="social__rule"></span>
    <span class="social__dot"></span>
    <span class="social__dot"></span>
  </div>
</main>
</body>
</html>
```